Carpet cleaning company focused on high quality needs business cards

We are a growing company that just merged with another company and need to design a new business card. We do both residential as well as commercial cleaning. We do carpet, tile & grout, upholstery, hard floors, and stain & pet odor removal. We treat our customers like family and strive to achieve outstanding results with every job.

```html
<!DOCTYPE html>
<html lang="en">
<head>
<meta charset="utf-8">
<title>Kestrel Floorcare – Business Card</title>
<link href="https://fonts.googleapis.com/css2?family=Open+Sans:wght@400;600;800&display=swap" rel="stylesheet">
<style>
  :root {
    --backdrop: #d6d6d6;
    --card: #ffffff;
    --ink: #1a1a1a;
    --wave-black: #161616;
    --brand-blue: #0b84c4;
    --brand-red: #ee4036;
    --on-dark: #ffffff;
  }
  * { margin: 0; padding: 0; box-sizing: border-box; }
  html, body {
    width: 1200px; height: 588px; overflow: hidden;
    background: var(--backdrop);
    font-family: "Open Sans", Arial, sans-serif;
  }
  .canvas { position: relative; width: 1200px; height: 588px; }
  .card {
    position: absolute; top: 141px;
    width: 488px; height: 289px;
    background: var(--card);
    border-radius: 19px; overflow: hidden;
  }
  .card--front { left: 87px; }
  .card--back { left: 622px; }

  .wave { position: absolute; inset: 0; width: 100%; height: 100%; }

  .brand { position: absolute; display: flex; align-items: center; white-space: nowrap; }
  .brand__square { background: var(--brand-red); flex: none; }
  .brand__name { color: var(--ink); font-weight: 800; line-height: 1; letter-spacing: -0.01em; }

  .card--front .brand { right: 20px; top: 74px; gap: 8px; }
  .card--front .brand__square { width: 14px; height: 14px; }
  .card--front .brand__name { font-size: 21px; }

  .card--back .brand { left: 0; right: 0; top: 124px; justify-content: center; gap: 14px; }
  .card--back .brand__square { width: 28px; height: 28px; }
  .card--back .brand__name { font-size: 40px; }

  .person { position: absolute; left: 20px; top: 146px; color: var(--on-dark); }
  .person__name { color: var(--brand-blue); font-size: 20px; font-weight: 600; letter-spacing: -0.01em; line-height: 1.1; }
  .person__role { font-size: 14px; line-height: 1.3; }

  .contact { position: absolute; left: 20px; top: 214px; list-style: none; color: var(--on-dark); font-size: 13px; line-height: 17.5px; }
  .contact li { display: flex; align-items: center; gap: 5px; }
  .contact svg { width: 11px; height: 11px; fill: var(--brand-blue); flex: none; }

  .address { position: absolute; right: 19px; top: 232px; color: var(--on-dark); font-size: 13px; line-height: 18px; text-align: right; font-style: normal; }
</style>
</head>
<body>
<div class="canvas">

  <section class="card card--front">
    <svg class="wave" viewBox="0 0 488 289" preserveAspectRatio="none" aria-hidden="true">
      <path fill="var(--brand-blue)" d="M60,92 C170,80 270,170 380,202 C432,216 466,200 488,180 L488,196 C466,214 430,222 380,214 C280,196 190,100 70,96 Z"/>
      <path fill="var(--wave-black)" stroke="#ffffff" stroke-width="2" d="M0,118 C30,98 70,90 120,96 C210,108 290,198 382,214 C432,222 466,212 488,200 L488,289 L0,289 Z"/>
    </svg>

    <div class="brand">
      <span class="brand__square" aria-hidden="true"></span>
      <span class="brand__name">Kestrel Floorcare</span>
    </div>

    <div class="person">
      <p class="person__name">MARCUS BELL</p>
      <p class="person__role">OWNER</p>
    </div>

    <ul class="contact">
      <li><svg viewBox="0 0 24 24"><path d="M6.6 10.8a15.1 15.1 0 0 0 6.6 6.6l2.2-2.2a1 1 0 0 1 1-.25 11.4 11.4 0 0 0 3.6.57 1 1 0 0 1 1 1V20a1 1 0 0 1-1 1A17 17 0 0 1 3 4a1 1 0 0 1 1-1h3.5a1 1 0 0 1 1 1c0 1.25.2 2.45.57 3.57a1 1 0 0 1-.25 1z"/></svg>123 456 789</li>
      <li><svg viewBox="0 0 24 24"><path d="M2 5h20v2l-10 6L2 7z M2 9l10 6 10-6v10H2z"/></svg>info@yourmail.com</li>
      <li><svg viewBox="0 0 24 24"><circle cx="12" cy="12" r="10"/></svg>www.yourwebsite.com</li>
    </ul>

    <address class="address">Your address, City<br>State, Zip 1234</address>
  </section>

  <section class="card card--back">
    <div class="brand">
      <span class="brand__square" aria-hidden="true"></span>
      <span class="brand__name">Kestrel Floorcare</span>
    </div>
  </section>

</div>
</body>
</html>
```